i would like a business card to leave with customers and potential customers for electrical work and for the supply and install of reverse cycle airconditioning in the domestic and commercial market.
I own my own business and im a sole trader. I have an a'class electrical lisence and also a refrigeration lisence so i am
able to offer complete installations in airconditioning by a fully qualified and lisenced tradesman.
im looking for something that comes across as unique and professional.
i had the coluor black and some gold in mind but open to any coluors.
something like Lanterra Electrical & Refrigeration
or Lanterra Air.
i will use this design on a business card to advertise through summer to help generate installs through the busy season.

Target Market(s)

Mainly domestic house holds through summer who are in need of airconditioning and reliable information to acomadate thier cooling and heating requirements

Industry/Entity Type

Electrical

Requirements
Must have
• Business name- Lanterra
My name- Mark Delford
My mobile no- 0438 517 290
My email- mrdelford@qelvo.com.au
Installation & Decomissioning of aiconditioning split systems
LIC NO: TRK 540316
Nice to have
• Lanterra Electrical & Refrigeration

```html
<!DOCTYPE html>
<html lang="en">
<head>
<meta charset="utf-8">
<title>Lanterra Electrical &amp; Refrigeration – Business Card</title>
<link rel="stylesheet" href="https://fonts.googleapis.com/css2?family=Roboto+Condensed:wght@300;400&display=swap">
<style>
  :root {
    --page: #ffffff;
    --card: #000000;
    --card-edge: #cfcfcf;
    --gold: #e9d46a;
    --gold-deep: #c4a312;
    --gold-light: #f6ec8e;
    --ghost: #1d1d1d;
    --contact: #c9c9c9;
    --band-text: #3b3b3b;
  }
  * { margin: 0; padding: 0; box-sizing: border-box; }
  html, body { width: 1200px; height: 901px; overflow: hidden; background: var(--page); }
  body { position: relative; font-family: "Roboto Condensed", "Arial Narrow", sans-serif; }

  .card {
    position: absolute;
    left: 276px;
    width: 657px;
    height: 371px;
    background: var(--card);
    border: 1px solid var(--card-edge);
    overflow: hidden;
  }
  .card--front { top: 57px; }
  .card--back { top: 476px; }

  .brand {
    position: absolute;
    left: 0; right: 0;
    top: 122px;
    text-align: center;
    color: var(--gold);
  }
  .brand__name {
    font-weight: 300;
    font-size: 74px;
    line-height: 1;
    letter-spacing: 2px;
  }
  .brand__descriptor {
    margin-top: 10px;
    font-weight: 400;
    font-size: 15px;
    letter-spacing: 1.5px;
  }

  .ghost-name {
    position: absolute;
    left: -10px;
    top: 40px;
    font-weight: 300;
    font-size: 190px;
    line-height: 1;
    color: var(--ghost);
    white-space: nowrap;
  }

  .contact {
    position: absolute;
    left: 0; right: 0;
    text-align: center;
    color: var(--contact);
    font-weight: 300;
    line-height: 1;
    white-space: nowrap;
  }
  .contact--name  { top: 180px; font-size: 27px; }
  .contact--phone { top: 213px; font-size: 27px; }
  .contact--email { top: 277px; font-size: 27px; }
  .contact--licence { top: 310px; font-size: 12px; font-weight: 400; }

  .service-band {
    position: absolute;
    left: 0; right: 0; bottom: 0;
    height: 38px;
    background: linear-gradient(90deg, var(--gold-deep) 0%, var(--gold) 55%, var(--gold-light) 100%);
    color: var(--band-text);
    font-size: 19px;
    font-weight: 400;
    line-height: 38px;
    text-align: center;
    text-transform: uppercase;
    white-space: nowrap;
  }
</style>
</head>
<body>
  <section class="card card--front" aria-label="Card front">
    <div class="brand">
      <div class="brand__name">Lanterra</div>
      <div class="brand__descriptor">ELECTRICAL &amp; REFRIGERATION</div>
    </div>
  </section>

  <section class="card card--back" aria-label="Card back">
    <div class="ghost-name" aria-hidden="true">Lanterra</div>
    <p class="contact contact--name">Mark Delford</p>
    <p class="contact contact--phone">0438 517 290</p>
    <p class="contact contact--email">mrdelford@qelvo.com.au</p>
    <p class="contact contact--licence">LIC NO: TRK 540316</p>
    <div class="service-band">Installation &amp; Decomissioning of Airconditioning Split Systems</div>
  </section>
</body>
</html>
```